Vindgerdi - Start-up company selling electricity

Hello let me tell you about Vindgerdi.

Vindgerdi is start-up company selling electricity in Iceland. The operations of the company consist of making power usage forecasts for our customers, purchasing the electricity wholesale from the energy producers, and selling the electricity to the consumer. We are focused on tech by using optimization and machine learning to minimize electricity prices to our customers. Our marketing strategy is to portray a tech company mindset and to show dedication to driving down the electricity price on the market.

We need your help to make our website pop. Possible concepts to work with are as follows:

- Iceland the land of ice and fire
- Green energy
- Innovation
- Tech and data science

Link to our website: https://prufa.vindgerdi-example.is/
We are open to ideas.
Thank you!

Target Market(s)

Electricity consumers both homes and companies.

Number of Pages Required

1 page

Font styles to use
Serif
Sans Serif

```html
<!DOCTYPE html>
<html lang="en">
<head>
<meta charset="utf-8">
<title>Vindgerdi – Selling And Generating Energy</title>
<link href="https://fonts.googleapis.com/css2?family=Rubik:wght@700&family=Montserrat:wght@400;500&family=Noto+Serif:wght@400;700&family=Source+Sans+3:wght@400;600&display=swap" rel="stylesheet">
<style>
:root{
  --red:#a3281f;
  --red-soft:#c0453b;
  --navy:#14305c;
  --ink:#1c2d4f;
  --grey-text:#5b5f66;
  --light-bg:#f1f2f4;
  --white:#ffffff;
}
*{margin:0;padding:0;box-sizing:border-box}
html,body{width:1200px;height:2812px;overflow:hidden;background:var(--white)}
body{position:relative;font-family:"Source Sans 3",sans-serif;color:var(--grey-text)}
.abs{position:absolute}
.serif{font-family:"Noto Serif",serif}

/* Hero */
.hero{position:absolute;left:0;top:0;width:1200px;height:713px;overflow:hidden;
  background:linear-gradient(180deg,#2c3038 0%,#414751 30%,#2f333a 62%,#15191b 82%,#0d100f 100%)}
.hero-photo{position:absolute;inset:0}
.brand{position:absolute;display:flex;align-items:center;gap:10px;font-family:"Noto Serif",serif;font-size:28px;color:var(--red);letter-spacing:.5px}
.brand-dot{width:22px;height:22px;border-radius:50%;background:var(--red)}
.nav{position:absolute;top:34px;right:62px;display:flex;gap:20px;font-family:"Source Sans 3",sans-serif;font-size:13px;color:var(--white)}
.nav a{color:inherit;text-decoration:none;padding:4px 2px;position:relative}
.nav .active{background:var(--red);border-radius:16px;padding:4px 12px;margin-right:-8px}
.hero-title{left:162px;top:158px;font-family:"Rubik",sans-serif;font-weight:700;font-size:62px;line-height:58px;color:var(--white);text-shadow:2px 3px 0 rgba(20,48,92,.8)}
.hero-sub{left:166px;top:347px;width:360px;font-family:"Montserrat",sans-serif;font-size:14.5px;line-height:21px;color:#e9e9e9}
.btn-solid{position:absolute;display:flex;align-items:center;justify-content:center;background:var(--red);color:var(--white);font-family:"Noto Serif",serif;font-size:15px;border-radius:4px}
.scroll{left:1106px;top:326px;transform-origin:left top;transform:rotate(-90deg) translateX(-84px);font-family:"Montserrat",sans-serif;font-size:14px;color:#ddd;white-space:nowrap}

/* About */
.about{position:absolute;left:0;top:713px;width:1200px;height:513px;background:var(--light-bg);overflow:hidden}
.h-red{color:var(--red);font-family:"Noto Serif",serif;font-weight:400}
.h-navy{color:var(--navy);font-family:"Noto Serif",serif;font-weight:700}
.pill{position:absolute;display:flex;align-items:center;gap:10px;padding:0 12px 0 21px;height:37px;border-radius:19px;color:var(--white);font-family:"Noto Serif",serif;font-size:14px;letter-spacing:.3px}
.pill.red{background:var(--red)}
.pill.navy{background:var(--navy)}
.pill .chev{width:20px;height:20px;border:1.5px solid var(--white);border-radius:50%;display:flex;align-items:center;justify-content:center}

/* Features */
.section-title{position:absolute;left:0;width:1200px;text-align:center;font-size:35px;line-height:42px}
.step-title{font-family:"Noto Serif",serif;font-weight:700;font-size:20px;color:var(--navy)}
.step-text{font-size:13.5px;line-height:20px;color:var(--grey-text)}
.price{font-family:"Noto Serif",serif;color:var(--red);font-size:25px}
.unit{font-size:11.5px;color:var(--grey-text)}

/* Footer */
.footer-col h4{font-family:"Noto Serif",serif;font-weight:700;font-size:16px;color:var(--white);margin-bottom:14px}
.footer-col ul{list-style:none;font-size:12px;color:#f4e4e2;line-height:25px}
.footer-col li{position:relative;padding-left:17px}
.footer-col li.dot::before{content:"";position:absolute;left:0;top:10px;width:5px;height:5px;border-radius:50%;background:var(--white)}
.footer-col li.icon{padding-left:27px;line-height:29px}
.footer-col li.icon svg{position:absolute;left:0;top:7px}
.divider{position:absolute;width:1px;background:rgba(255,255,255,.25)}
</style>
</head>
<body>

<section class="hero">
  <div class="hero-photo" role="img" aria-label="Photo of a high-voltage transmission tower against a cloudy dusk sky above a line of palm trees"></div>
  <svg class="abs" style="left:0;top:0" width="1200" height="713">
    <circle cx="272" cy="176" r="357" fill="rgba(10,12,16,.35)" stroke="rgba(163,40,31,.75)" stroke-width="14"/>
    <line x1="1125" y1="420" x2="1125" y2="538" stroke="rgba(255,255,255,.5)"/>
    <line x1="1016" y1="663" x2="1052" y2="663" stroke="rgba(255,255,255,.5)"/>
    <circle cx="1073" cy="663" r="18" fill="var(--red)"/>
    <path d="M1077 655 l-8 8 l8 8" fill="none" stroke="#fff" stroke-width="2"/>
    <circle cx="1117" cy="663" r="20" fill="none" stroke="rgba(255,255,255,.75)" stroke-width="1.3"/>
    <path d="M1114 655 l8 8 l-8 8" fill="none" stroke="#fff" stroke-width="2"/>
  </svg>
  <div class="brand" style="left:60px;top:26px"><span class="brand-dot"></span>VINDGERDI</div>
  <nav class="nav">
    <a class="active">Terms of Business</a>
    <a>Question &amp; Answer</a>
    <a>About Vindgerdi</a>
    <a>Contact Us</a>
  </nav>
  <h1 class="abs hero-title">Selling And<br>Generating<br>Energy</h1>
  <p class="abs hero-sub">Everything you need to know about how we can help you sell electricity</p>
  <a class="btn-solid" style="left:166px;top:401px;width:146px;height:41px">REGISTER NOW</a>
  <div class="abs scroll">Scroll Down</div>
</section>

<section class="about">
  <svg class="abs" style="left:0;top:0" width="1200" height="513">
    <circle cx="1000" cy="60" r="305" fill="none" stroke="rgba(163,40,31,.55)" stroke-width="1"/>
    <circle cx="1000" cy="60" r="291" fill="none" stroke="rgba(163,40,31,.35)" stroke-width="1"/>
    <circle cx="858" cy="288" r="164" fill="var(--navy)"/>
    <defs>
      <radialGradient id="bulbGlow" cx="70%" cy="30%" r="80%">
        <stop offset="0" stop-color="#f2e1a0"/>
        <stop offset=".35" stop-color="#9bb54a"/>
        <stop offset=".75" stop-color="#4f6d26"/>
        <stop offset="1" stop-color="#2c2418"/>
      </radialGradient>
      <linearGradient id="windSky" x1="0" y1="0" x2="1" y2="1">
        <stop offset="0" stop-color="#7fb3d8"/>
        <stop offset=".6" stop-color="#5c7f7a"/>
        <stop offset="1" stop-color="#6a6a3a"/>
      </linearGradient>
    </defs>
    <circle cx="826" cy="262" r="150" fill="url(#bulbGlow)" role="img" aria-label="Light bulb glowing beside a young green seedling in soil"/>
    <circle cx="1185" cy="126" r="94" fill="none" stroke="rgba(163,40,31,.35)"/>
    <circle cx="1185" cy="126" r="89" fill="none" stroke="rgba(163,40,31,.25)"/>
    <circle cx="1185" cy="126" r="82" fill="url(#windSky)" role="img" aria-label="Aerial view of wind turbines along a coastline"/>
  </svg>
  <h2 class="abs serif" style="left:148px;top:70px;font-size:36px;line-height:42px">
    <span class="h-red">About</span><br><span class="h-navy">Vindgerdi</span>
  </h2>
  <p class="abs serif" style="left:149px;top:168px;width:380px;font-size:14.5px;line-height:21px;color:#2b2f38">What is Vindgerdi's unique position in the electricity sales market?</p>
  <p class="abs" style="left:149px;top:222px;width:390px;font-size:13px;line-height:21px">Vindgerdi uses automation and artificial intelligence to achieve lower prices in the electricity market. Our goal is to minimize the cost of energy sales, promote energy balance and offer good service.</p>
  <p class="abs" style="left:149px;top:292px;width:392px;font-size:13px;line-height:21px">Vindgerdi's goal is to offer its customers the most favorable electricity prices in Iceland. Electricity is part of the monthly costs of households and companies, and by doing business with Vindgerdi, savings can be achieved and operating costs reduced.</p>
  <a class="pill red" style="left:148px;top:390px">LEARN MORE <span class="chev"><svg width="8" height="10"><path d="M2 1l4 4-4 4" fill="none" stroke="#fff" stroke-width="1.5"/></svg></span></a>
</section>

<!-- Red lower band with white curved top -->
<svg class="abs" style="left:0;top:2150px" width="1200" height="662">
  <rect x="0" y="0" width="1200" height="662" fill="var(--red)"/>
  <path d="M0 0 L1200 0 L1200 28 C1080 230 860 400 600 405 C340 408 140 320 0 247 Z" fill="var(--white)"/>
</svg>

<section class="features">
  <svg class="abs" style="left:0;top:1226px" width="1200" height="1040">
    <circle cx="600" cy="83" r="14" fill="var(--navy)"/>
    <path d="M318 445 V491 H880 V535" fill="none" stroke="var(--red)" stroke-width="1"/>
    <path d="M880 723 V769 H318 V813" fill="none" stroke="var(--red)" stroke-width="1"/>
    <g fill="var(--red)">
      <circle cx="318" cy="445" r="3"/><circle cx="880" cy="535" r="3"/>
      <circle cx="880" cy="723" r="3"/><circle cx="318" cy="813" r="3"/>
    </g>
    <g fill="none" stroke="rgba(163,40,31,.3)">
      <circle cx="318" cy="351" r="102"/><circle cx="318" cy="351" r="97"/><circle cx="318" cy="351" r="92"/>
      <circle cx="880" cy="628" r="102"/><circle cx="880" cy="628" r="97"/><circle cx="880" cy="628" r="92"/>
      <circle cx="318" cy="906" r="102"/><circle cx="318" cy="906" r="97"/><circle cx="318" cy="906" r="92"/>
    </g>
    <circle cx="318" cy="351" r="75" fill="var(--navy)"/>
    <circle cx="880" cy="628" r="75" fill="var(--navy)"/>
    <circle cx="318" cy="906" r="75" fill="var(--navy)"/>
    <g fill="none" stroke="#fff" stroke-width="2.5" stroke-linecap="round" stroke-linejoin="round">
      <path d="M310 325 l26 26 l-12 12 a18 18 0 0 1 -26 -26 z"/>
      <path d="M322 333 l12 -12 M330 341 l12 -12"/>
      <circle cx="311" cy="350" r="5"/>
      <path d="M298 363 l-10 10 a8 8 0 0 1 -11 11 a6 6 0 0 1 8 -8"/>
    </g>
    <g fill="none" stroke="#fff" stroke-width="2.5" stroke-linejoin="round">
      <path d="M862 588 h42 v52 M862 588 v82 h28"/>
      <path d="M852 598 v82 h28" opacity=".9"/>
      <path d="M870 602 h26 M870 614 h26 M870 626 h26 M870 638 h16 M870 650 h12"/>
      <path d="M918 630 l-26 30 l-4 10 l10 -4 l26 -30 z"/>
    </g>
    <g fill="none" stroke="#fff" stroke-width="2.5" stroke-linejoin="round">
      <path d="M306 872 h24 M302 890 h32 M292 884 h52 M288 902 h60 M306 872 l-10 72 M330 872 l10 72 M302 890 l28 18 M334 890 l-28 18 M300 918 l36 26 M336 918 l-36 26 M318 866 v6"/>
      <path d="M292 884 v6 M344 884 v6 M288 902 v6 M348 902 v6"/>
    </g>
  </svg>

  <h2 class="section-title serif" style="top:1346px"><span class="h-red">Same Electricity</span><br><span class="h-navy">~ Just Cheaper!</span></h2>

  <div class="abs" style="left:487px;top:1502px;width:292px">
    <h3 class="step-title">Welcome To Business</h3>
    <p class="step-text" style="margin-top:8px">it can be said that by trading with Vindgerdi, you support the development of the Icelandic electricity market.</p>
  </div>
  <a class="pill red" style="left:486px;top:1608px">REGISTER <span class="chev"><svg width="8" height="10"><path d="M2 1l4 4-4 4" fill="none" stroke="#fff" stroke-width="1.5"/></svg></span></a>
  <a class="pill navy" style="left:620px;top:1608px">COMPANY <span class="chev"><svg width="8" height="10"><path d="M2 1l4 4-4 4" fill="none" stroke="#fff" stroke-width="1.5"/></svg></span></a>

  <div class="abs" style="left:480px;top:1790px;width:248px;text-align:right">
    <h3 class="step-title">Price List</h3>
    <div style="margin-top:22px;display:flex;justify-content:flex-end;align-items:baseline;gap:8px">
      <span class="price">6.95</span><span class="unit">ISK/kWh</span>
      <span style="display:inline-block;width:1px;height:26px;background:#888;margin:0 2px;align-self:center"></span>
      <span class="price">6.22</span><span class="unit">ISK/kWh</span>
    </div>
    <p class="step-text" style="margin-top:14px;font-size:13px">Electric Acceleration</p>
    <p style="margin-top:2px;font-size:14.5px;color:#2b2f38">Make a price comparison</p>
  </div>

  <div class="abs" style="left:487px;top:2079px;width:280px">
    <h3 class="step-title">The Future Is Exciting</h3>
    <p class="step-text" style="margin-top:8px">Let's make the electricity system smarter together. Vindgerdi uses artificial intelligence, data science and automation to minimize costs and promote eccentricity</p>
  </div>
</section>

<section class="choose">
  <svg class="abs" style="left:584px;top:2302px" width="32" height="32"><circle cx="16" cy="16" r="14" fill="var(--navy)"/></svg>
  <h2 class="section-title serif" style="top:2353px;font-size:29px;line-height:36px"><span class="h-red">You Choose Where You</span><br><span class="h-navy">Buy Electricity</span></h2>
  <a class="pill red" style="left:536px;top:2434px">VERDVAKT <span class="chev"><svg width="8" height="10"><path d="M2 1l4 4-4 4" fill="none" stroke="#fff" stroke-width="1.5"/></svg></span></a>
</section>

<footer>
  <div class="divider" style="left:325px;top:2540px;height:226px"></div>
  <div class="divider" style="left:600px;top:2480px;height:286px"></div>
  <div class="divider" style="left:875px;top:2480px;height:286px"></div>

  <div class="brand" style="left:60px;top:2604px;color:var(--white)"><span class="brand-dot" style="background:var(--white)"></span>VINDGERDI</div>
  <p class="abs" style="left:61px;top:2650px;width:230px;font-size:12px;line-height:21px;color:#f4e4e2">Vindgerdi uses automation and artificial intelligence to achieve lower prices in the electricity market.</p>

  <div class="abs footer-col" style="left:336px;top:2604px">
    <h4>Sitemap</h4>
    <ul><li class="dot">Terms of Business</li><li class="dot">Question &amp; Answer</li><li class="dot">About Vindgerdi</li></ul>
  </div>

  <div class="abs footer-col" style="left:612px;top:2604px">
    <h4>Contact Us</h4>
    <ul>
      <li class="icon"><svg width="14" height="16"><path d="M7 15 C2 9 2 7 2 6 a5 5 0 0 1 10 0 c0 1 0 3 -5 9z" fill="none" stroke="#fff" stroke-width="1.5"/><circle cx="7" cy="6" r="2" fill="#fff"/></svg>Lindargata 42 101 Reykjavík</li>
      <li class="icon"><svg width="15" height="12"><rect x="1" y="1" width="13" height="10" fill="#fff"/><path d="M1 1 l6.5 5 l6.5 -5" fill="none" stroke="var(--red)" stroke-width="1.3"/></svg>hallo@vindgerdi-example.is</li>
      <li class="icon" style="font-size:16px"><svg width="15" height="15"><path d="M3 1 l3 0 l1.5 4 l-2 1.5 a9 9 0 0 0 4 4 l1.5 -2 l4 1.5 l0 3 a2 2 0 0 1 -2 2 A13 13 0 0 1 1 3 a2 2 0 0 1 2 -2z" fill="#fff"/></svg>555-0199</li>
    </ul>
  </div>

  <div class="abs footer-col" style="left:887px;top:2604px">
    <h4>More Info</h4>
    <ul style="font-size:11.5px;line-height:24px"><li class="dot">Vindgerdi ehf</li><li class="dot">ID number: 610221-0870</li><li class="dot">VAT number: 142317</li></ul>
  </div>

  <div class="abs" style="left:60px;top:2768px;width:1080px;height:1px;background:rgba(255,255,255,.3)"></div>
  <p class="abs" style="left:0;top:2782px;width:1200px;text-align:center;font-size:11.5px;color:#f4e4e2">©<strong>Vindgerdi</strong> - 2021 all right rserved.</p>
</footer>

</body>
</html>
```